Bulldog themed background for Real Estate Purchase Letter

I need a phantom background or watermark on a standard 8 1/2" x 11" paper. I am going to put a letter over the background. I want a bulldog theme that is cute, funny and original. This letter is for a real estate project and we want to capture the person sub-consciously . Attached is my personal dogs. If you want to use them you can but not required. I have attached the letter that I am trying to emulate. I want bulldogs not horses.

Target Market(s)

45 years old and higher

Industry/Entity Type

Real Estate

Font styles to use
Serif
Sans Serif

Colors

Designer to choose colors to be used in the design.

Requirements
Must have
• fun, happiness, reassuring,
Should not have
• violence, negativity, unhappy

```html
<!DOCTYPE html>
<html lang="en">
<head>
<meta charset="utf-8">
<title>Property Purchase Letter</title>
<link rel="stylesheet" href="https://fonts.googleapis.com/css2?family=Open+Sans:wght@300;400;600&family=Montserrat:wght@400;500&display=swap">
<style>
  :root {
    --brand-blue: #1f5fb0;
    --brand-sky: #1fb6f0;
    --brand-deep: #0d4fd6;
    --ink: #333333;
    --ink-strong: #2a2a2a;
    --mascot-tone: #d9d9d9;
    --paper: #ffffff;
  }
  * { margin: 0; padding: 0; box-sizing: border-box; }
  html, body { width: 850px; height: 1200px; overflow: hidden; background: var(--paper); }
  .letter {
    position: relative; width: 850px; height: 1200px; overflow: hidden;
    background: var(--paper); color: var(--ink);
    font-family: "Open Sans", Arial, sans-serif; font-weight: 300;
  }
  .wave { position: absolute; }
  .wave-top { left: 0; top: 0; }
  .wave-bottom { right: 0; bottom: 0; }
  .mascot-watermark { position: absolute; left: 30px; top: 180px; }
  .agent-band {
    position: absolute; left: 458px; top: 44px; width: 392px; height: 34px;
    background: var(--brand-blue); color: #fff;
    font-family: "Montserrat", Arial, sans-serif; font-weight: 500; font-size: 17.5px;
    display: flex; align-items: center; padding-left: 14px; letter-spacing: 0.2px;
  }
  .recipient {
    position: absolute; left: 69px; top: 114px;
    font-size: 18px; line-height: 30px;
  }
  .recipient .name { font-weight: 400; color: var(--ink-strong); }
  .greeting { position: absolute; left: 69px; top: 248px; font-size: 18px; }
  .greeting strong, .body strong { font-weight: 400; color: var(--ink-strong); }
  .body {
    position: absolute; left: 69px; top: 318px; width: 711px;
    font-size: 17.6px; line-height: 36.6px; text-align: justify;
  }
  .body p { text-indent: 40px; margin-bottom: 36px; }
  .closing { position: absolute; left: 69px; top: 1012px; font-size: 18px; }
  .signature {
    position: absolute; left: 69px; top: 1085px; font-size: 18px;
    font-weight: 400; color: var(--ink-strong);
  }
  .contact-list {
    position: absolute; right: 72px; top: 1012px; list-style: none;
    font-family: "Montserrat", Arial, sans-serif; font-size: 15px; color: var(--ink);
  }
  .contact-list li {
    display: flex; justify-content: flex-end; align-items: center;
    gap: 9px; height: 31px; margin-bottom: 6px;
  }
  .contact-icon {
    width: 31px; height: 31px; background: var(--brand-blue);
    display: flex; align-items: center; justify-content: center;
  }
</style>
</head>
<body>
<main class="letter">
  <svg class="wave wave-top" width="470" height="160" viewBox="0 0 470 160" aria-hidden="true">
    <path d="M0 0 H470 C330 40 140 50 0 150 Z" fill="var(--brand-sky)"/>
    <path d="M0 0 H300 C200 20 70 70 0 110 Z" fill="var(--brand-deep)"/>
  </svg>

  <svg class="mascot-watermark" role="img" aria-label="Faint bulldog illustration watermark" width="800" height="860" viewBox="0 0 800 860">
    <defs>
      <radialGradient id="mascot-fade" cx="50%" cy="50%" r="55%">
        <stop offset="0%" stop-color="var(--mascot-tone)" stop-opacity="0.55"/>
        <stop offset="100%" stop-color="var(--mascot-tone)" stop-opacity="0.15"/>
      </radialGradient>
    </defs>
    <ellipse cx="400" cy="430" rx="390" ry="420" fill="url(#mascot-fade)"/>
  </svg>

  <div class="agent-band">Real Estate Agent ID : #0000123456</div>

  <address class="recipient" style="font-style:normal">
    <div class="name">Mr. Sample Homeowner</div>
    <div>4521 Maple Lane</div>
    <div>Brookfield FL 34400-0000</div>
  </address>

  <p class="greeting">Dear <strong>First Name</strong></p>

  <section class="body">
    <p>I am writing you, because I am interested in purchasing your property located at <strong>4521 Maple Lane Brookfield FL 34400-0000</strong> I live nearby in Cedarville and I puschages properties throught the state of PA Currently I am working on projects in the neighbourhood, which is how I learned of your property.</p>
    <p>Please call me at <strong>(XXX) XXXX-Local#</strong> so I can tell you how we can buy your property quickly, with no hassels and most importantly, at a fair price. I purchase the hous directly from you so there are no real estate commissions or extra fees coming out of your pocket. Furthermore, I always make cash offers so you never have to worry about delays resulting from a buyer trying to qualify for a mortgage and wasting your valuable time.</p>
    <p>I'will be glade to personally tell you more about how we can work together. All call are completely confidential and there is no obligation whatsoever. Even if you are not intersted in selling at thing time call <strong>(xxx) xxxx-xxxx</strong>, so I can help you with determining the value of your property. You should also keep this letter for your future reference, since things in life have a tendency to change unexpectedly. Thanks you for your time and consideration and I look forward to speaking with you.</p>
  </section>

  <p class="closing">Sincerely,</p>
  <p class="signature">Dana Whitfield</p>

  <ul class="contact-list">
    <li>+1 555 010 4821
      <span class="contact-icon"><svg width="17" height="17" viewBox="0 0 24 24" aria-hidden="true"><path d="M6.6 10.8a15 15 0 0 0 6.6 6.6l2.2-2.2a1 1 0 0 1 1-.25 11.4 11.4 0 0 0 3.6.6 1 1 0 0 1 1 1V20a1 1 0 0 1-1 1A17 17 0 0 1 3 4a1 1 0 0 1 1-1h3.5a1 1 0 0 1 1 1c0 1.25.2 2.45.6 3.6a1 1 0 0 1-.25 1z" fill="#fff"/></svg></span>
    </li>
    <li>www.cedarhomebuyers.com
      <span class="contact-icon"><svg width="17" height="17" viewBox="0 0 24 24" aria-hidden="true"><circle cx="12" cy="12" r="9" fill="none" stroke="#fff" stroke-width="2"/><path d="M3 12h18M12 3c3 3 3 15 0 18M12 3c-3 3-3 15 0 18" fill="none" stroke="#fff" stroke-width="1.6"/></svg></span>
    </li>
    <li>Address Line Here, Address Line Here
      <span class="contact-icon"><svg width="15" height="17" viewBox="0 0 24 24" aria-hidden="true"><path d="M12 2a7 7 0 0 0-7 7c0 5 7 13 7 13s7-8 7-13a7 7 0 0 0-7-7zm0 9.5A2.5 2.5 0 1 1 12 6.5a2.5 2.5 0 0 1 0 5z" fill="#fff"/></svg></span>
    </li>
  </ul>

  <svg class="wave wave-bottom" width="420" height="90" viewBox="0 0 420 90" aria-hidden="true">
    <path d="M420 0 V90 H0 C140 40 300 20 420 0 Z" fill="var(--brand-sky)"/>
    <path d="M420 40 V90 H150 C250 60 340 50 420 40 Z" fill="var(--brand-deep)"/>
  </svg>
</main>
</body>
</html>
```